Business Card Design for my Real Estate Investing Company

This is for a Real Estate Investing Company that will be serving the Las Vegas Valley. Id like the following slogan included: "Investing in Our Community" I have attached my logo. You will see the color tones I'm interested in..in my logo. I would like the card to be double-sided with a modern, professional look.
Target Market(s)
Homeowners, banks, real estate industry
Industry/Entity Type
Real Estate
Contact Information for Business Card
name: Dale Harwick
position: Managing Member
address: 4821 Corliss Pkwy ste 207-300
N. Las Vegas, NV 89084
phone: (702) 555-0143
fax: (702) 555-0187
email: SummitRidgeEstate@hollowmail.test
web: SummitRidgeEstates.test
*At the bottom of the card I would like....
We buy houses for cash....no repairs, no commissions, no fees!
Logo Text
SUMMIT RIDGE ESTATES "Investing in Our Community"
Font styles to use
Other font styles liked:
- Lora
Requirements
Must have
- On the back of the card, i'd like to have my logo large and the following statements:
- Are you considering selling your home? Want a simple, hassle-free transaction? We can help! We buy houses for cash and can close quickly! No need to do any repairs, no realtor commissions, no closing costs.....and no headaches. Let us help you with your real estate needs...!
Nice to have
- multiple colors 2 two tone on front and back

```html
<!DOCTYPE html>
<html lang="en">
<head>
<meta charset="utf-8">
<title>Summit Ridge Estates – Business Card</title>
<link rel="stylesheet" href="https://fonts.googleapis.com/css2?family=Lora:ital,wght@0,400;0,700;1,400&display=swap">
<style>
  :root {
    --brand-blue: #0b55a3;
    --ink-grey: #555555;
    --paper: #ffffff;
    --backdrop: #2a2a2a;
    --rule: #3f7cc4;
  }
  * { box-sizing: border-box; margin: 0; padding: 0; }
  html, body { width: 1200px; height: 1000px; overflow: hidden; }
  body {
    background: var(--backdrop);
    font-family: "Lora", Georgia, serif;
    position: relative;
  }
  .card {
    position: absolute;
    left: 246px;
    width: 709px;
    height: 404px;
    background: var(--paper);
    overflow: hidden;
  }
  .card--front { top: 78px; }
  .card--back { top: 517px; }

  /* Front */
  .front-field {
    position: absolute; left: 0; top: 0; width: 100%; height: 350px;
    background: var(--brand-blue);
  }
  .front-wordmark {
    position: absolute; left: 0; right: 0; top: 168px;
    text-align: center; color: var(--paper);
    font-size: 50px; font-weight: 400; letter-spacing: 1px;
  }
  .front-slogan {
    position: absolute; left: 0; right: 0; top: 238px;
    text-align: center; color: var(--paper);
    font-style: italic; font-size: 17px; letter-spacing: 5px;
  }
  .front-web {
    position: absolute; left: 0; right: 0; top: 365px;
    text-align: center; color: var(--brand-blue); font-size: 17px;
  }

  /* Back */
  .back-wordmark {
    position: absolute; right: 34px; top: 82px;
    color: var(--brand-blue); font-size: 34px; font-weight: 400;
    text-align: right;
  }
  .back-slogan {
    position: absolute; right: 34px; top: 124px;
    color: #222; font-style: italic; font-size: 13px; letter-spacing: 2.4px;
  }
  .person { position: absolute; left: 33px; top: 162px; }
  .person-name { color: var(--brand-blue); font-weight: 700; font-size: 21px; }
  .person-title { color: var(--ink-grey); font-size: 16px; margin-top: 2px; }
  .divider {
    position: absolute; left: 33px; right: 34px; top: 219px;
    height: 1px; background: var(--rule);
  }
  .contact-list {
    position: absolute; left: 33px; top: 230px; list-style: none;
    color: var(--ink-grey); font-size: 17px; line-height: 22.5px;
  }
  .contact-list li { display: flex; align-items: center; gap: 6px; }
  .contact-list svg { width: 13px; height: 13px; fill: var(--brand-blue); flex: none; }
  .address {
    position: absolute; right: 34px; top: 275px; text-align: right;
    color: var(--ink-grey); font-size: 17px; line-height: 22.5px; font-style: normal;
  }
  .offer-band {
    position: absolute; left: 0; bottom: 0; width: 100%; height: 54px;
    background: var(--brand-blue); color: var(--paper);
    font-style: italic; font-size: 20px; letter-spacing: 1.2px;
    display: flex; align-items: center; padding-left: 33px;
  }
</style>
</head>
<body>

<section class="card card--front">
  <div class="front-field">
    <p class="front-wordmark">SUMMIT RIDGE ESTATES</p>
    <p class="front-slogan">"Investing in Our Community"</p>
  </div>
  <p class="front-web">www.SummitRidgeEstates.test</p>
</section>

<section class="card card--back">
  <p class="back-wordmark">SUMMIT RIDGE ESTATES</p>
  <p class="back-slogan">"Investing in Our Community"</p>

  <div class="person">
    <p class="person-name">Dale Harwick</p>
    <p class="person-title">Managing Member</p>
  </div>
  <div class="divider"></div>

  <ul class="contact-list">
    <li>
      <svg viewBox="0 0 16 16" aria-hidden="true"><path d="M3.6 1.2l2.3 2.8-1.3 1.8c.9 2 2.5 3.6 4.6 4.6l1.8-1.3 2.8 2.3-1.4 2.4C7.4 13.5 2.5 8.6 1.2 3.6z"/></svg>
      (702) 555-0143
    </li>
    <li>
      <svg viewBox="0 0 16 16" aria-hidden="true"><path d="M4 1h8v4H4zM1 6h14v6h-3v3H4v-3H1zm4 4v3.5h6V10z"/></svg>
      (702) 555-0187
    </li>
    <li>
      <svg viewBox="0 0 16 16" aria-hidden="true"><path d="M1 3h14v1L8 9 1 4zm0 2.5l7 5 7-5V13H1z"/></svg>
      SummitRidgeEstate@hollowmail.test
    </li>
    <li>
      <svg viewBox="0 0 16 16" aria-hidden="true"><path d="M8 1a7 7 0 100 14A7 7 0 008 1zm0 1.4c.8.9 1.4 2.2 1.6 3.6H6.4C6.6 4.6 7.2 3.3 8 2.4zM2.5 7h2.8c0 .7 0 1.3.1 2H2.5a5.6 5.6 0 010-2zm.5 3h2.6c.2 1.2.6 2.3 1.1 3.1A5.6 5.6 0 013 10zm3.4 0h3.2c-.2 1.3-.8 2.5-1.6 3.6-.8-1.1-1.4-2.3-1.6-3.6zm3.9 3.1c.5-.8.9-1.9 1.1-3.1H13a5.6 5.6 0 01-2.7 3.1zM13.5 9h-2.9c.1-.7.1-1.3.1-2h2.8a5.6 5.6 0 010 2zM6.3 7h3.4c0 .7 0 1.3-.1 2H6.4c-.1-.7-.1-1.3-.1-2zM13 6h-2.4c-.2-1.2-.6-2.3-1.1-3.1A5.6 5.6 0 0113 6zM6.5 2.9C6 3.7 5.6 4.8 5.4 6H3a5.6 5.6 0 013.5-3.1z"/></svg>
      SummitRidgeEstates.test
    </li>
  </ul>

  <address class="address">
    4821 Corliss Pkwy ste 207-300<br>
    N. Las Vegas, NV 89084
  </address>

  <p class="offer-band">We buy houses for cash....no repairs, no commissions, no fees!</p>
</section>

</body>
</html>
```